quickdeedsale.com redesign with wireframes, white space and custom form are very important

Need a new two column design that will convert easily to mobile responsive. Lots of white space. Winning design will probably be based on header area and making the custom form stand out. I want the header to be very much like www.tallgatevk.com except the form not to go up into the header.
Here are some of the websites I really like:
www.birchdwell.com
http://ourplotpurchasedirect.com/
http://kellbrightproperty.com/

We buy homes for cash and close fast. Our target is a home seller who is desperate to sell quickly.
I have uploaded my really ugly wireframe and my logo. I also uploaded my photo for the about us box and a possible photo to use for the header.
The copy on the wireframe is what I will be using except for the about us box.

Here is the exact link for video to frame in the top left box.
https://clipvault.example/Qm38pzrtLa

0592cd
85cae6
eaf1f7
fbee3d
ec1f27

• Everything on wireframe.
• Must use Verdana font and nothing should be smaller than 12 point. Most should be in 14 point. (except maybe inside of form)

```html
<!DOCTYPE html>
<html lang="en">
<head>
<meta charset="utf-8">
<title>quickdeedsale.com – Sell your home for cash</title>
<link rel="stylesheet" href="https://fonts.googleapis.com/css2?family=Open+Sans:wght@400;600;700&display=swap">
<style>
:root{
  --red:#ec1f27;
  --deep-blue:#0592cd;
  --sky:#85cae6;
  --mist:#eaf1f7;
  --yellow:#fbee3d;
  --form-yellow:#f8db4e;
  --ink:#222;
  --text:#444;
  --muted:#888;
  --panel:#f4f4f4;
  --line:#dcdcdc;
  --footer:#2b2b2b;
  --footer-text:#c9c9c9;
}
*{box-sizing:border-box;margin:0;padding:0}
html,body{width:1200px;height:2687px;overflow:hidden;background:#fff}
body{font-family:"Open Sans",sans-serif;color:var(--text);font-size:14px;line-height:1.5;position:relative}
a{color:inherit;text-decoration:none}
ul{list-style:none}

/* header */
.site-header{position:absolute;left:98px;top:0;width:1002px;height:131px}
.brand{position:absolute;left:0;top:40px;display:flex;align-items:center;gap:10px;font-size:24px;font-weight:700;color:var(--red)}
.brand-mark{width:22px;height:22px;background:var(--red);border-radius:3px}
.call{position:absolute;right:0;top:26px;text-align:right;padding-right:46px}
.call-label{font-size:16px;color:var(--ink)}
.call-label small{font-size:12px;color:var(--muted);margin-left:4px}
.call-number{display:block;font-size:24px;color:var(--red);line-height:1.1}
.call-icon{position:absolute;right:0;top:8px;width:34px;height:34px;border:1px solid #bbb;border-radius:50%;display:flex;align-items:center;justify-content:center}
.main-nav{position:absolute;right:0;top:90px;display:flex;gap:52px;font-size:14px;color:#666}
.main-nav .active{color:var(--red)}

/* hero */
.hero{position:absolute;left:98px;top:131px;width:1002px;height:344px;background:linear-gradient(180deg,#3d6fb8 0%,#7fa2cf 30%,#e8e3d8 45%,#cfc7b8 62%,#4f6a3a 78%,#2f4a22 100%)}
.hero-arrow{position:absolute;top:155px;width:20px;height:34px;display:flex;align-items:center;justify-content:center}
.hero-arrow.prev{left:6px}.hero-arrow.next{right:6px}
.hero-caption{position:absolute;left:22px;top:250px;background:rgba(20,20,20,.72);padding:8px 16px 8px 18px}
.hero-caption p{font-size:22px;color:#fff;line-height:1.3}
.hero-caption p.accent{color:var(--red);font-size:24px}

/* panels */
.panel{position:absolute;background:var(--panel);border:1px solid var(--line)}
.panel.white{background:#fff}
.col-left{left:98px;width:490px}
.col-right{left:610px;width:490px}
h2.red{color:var(--red);font-weight:400;font-size:19px;line-height:1.35}

/* benefits */
.benefits{top:487px;height:606px;padding:26px 20px}
.benefit-list{margin-top:20px}
.benefit-list li{display:flex;align-items:center;gap:12px;font-size:14px;color:var(--ink);height:50px}
.video-intro{margin-top:34px;font-size:13px;color:var(--ink)}
.video{margin-top:10px;width:446px;height:300px;background:linear-gradient(160deg,#6d7f8a 0%,#3f4c55 45%,#1d2328 100%);display:flex;align-items:center;justify-content:center}

/* form */
.lead-form{position:absolute;left:610px;top:487px;width:478px;height:606px;background:var(--form-yellow)}
.form-ribbon{position:absolute;right:-12px;top:10px;width:352px;height:66px;background:var(--red);color:#fff;text-align:center;padding-top:10px;box-shadow:0 2px 3px rgba(0,0,0,.15)}
.form-ribbon strong{display:block;font-size:17px;font-weight:400}
.form-ribbon span{font-size:12px}
.form-ribbon::after{content:"";position:absolute;right:0;bottom:-10px;border-top:10px solid #a3141a;border-right:12px solid transparent}
.fields{position:absolute;left:22px;top:107px;width:446px}
.field{height:47px;background:#fff;border:1px solid #eee;margin-bottom:13px;padding:0 18px;display:flex;align-items:center;font-size:12px;color:#999}
.submit{position:absolute;left:22px;top:538px;width:446px;height:44px;background:linear-gradient(#3a3a3a,#1c1c1c);color:#fff;font-size:13px;display:flex;align-items:center;justify-content:center;gap:10px;letter-spacing:.3px}

/* about selling */
.selling{top:1110px;height:498px;padding:24px 22px}
.selling h1{font-size:17px;font-weight:400;color:var(--ink);line-height:1.4}
.selling .lead{font-size:12px;line-height:1.6;margin-top:8px;color:#555}
.selling hr{border:0;border-top:1px solid var(--line);margin:14px -22px 18px}
.reasons{margin-top:12px}
.reasons li{font-size:12.5px;color:var(--ink);height:27px;padding-left:14px;position:relative}
.reasons li::before{content:"";position:absolute;left:0;top:8px;width:5px;height:5px;border-radius:50%;background:var(--ink)}
.help{margin-top:12px;font-size:19px;color:var(--red);line-height:1.4}

.contact-strip{top:1110px;height:122px;background:#fff}
.privacy{display:flex;align-items:center;gap:8px;padding:18px 20px 0;font-size:12px;color:var(--ink)}
.dot{width:26px;height:26px;border-radius:50%;display:inline-block}
.contact-strip hr{border:0;border-top:1px solid var(--line);margin:16px 20px 0}
.hours{padding:12px 20px;font-size:15px;color:#555}

.testimonials{top:1248px;height:174px;background:#fff;padding:16px 20px}
.testimonials blockquote{margin-top:14px;font-style:italic;font-size:13px;color:#444;line-height:1.6;position:relative;padding-left:26px}
.testimonials blockquote::before{content:"\201C";position:absolute;left:0;top:-8px;font-size:34px;font-style:normal;color:#555}
.author{display:flex;justify-content:space-between;margin-top:12px;font-size:14px;color:var(--ink)}
.author small{font-size:12px;color:var(--muted)}

.about{top:1440px;height:170px;background:#fff;padding:16px 18px;display:flex;gap:18px}
.about .portrait{width:120px;height:140px;background:linear-gradient(180deg,#9cb6c9,#6d8193);flex:none}
.about p{font-size:13px;color:#555;margin-top:6px}

/* listings */
.listing{height:172px;padding:20px 20px;display:flex;gap:16px}
.listing .photo{width:168px;height:124px;flex:none}
.listing h3{font-size:13px;font-weight:400;color:var(--ink);line-height:1.5}
.listing p{font-size:12px;color:#999;line-height:1.5;margin-top:8px}
.listing .more{font-size:12px;color:#888;margin-top:6px;display:block}

.cities{top:1630px;height:538px;background:#fff;padding:16px 20px}
.cities .intro{font-size:13px;color:#555;margin-top:8px;line-height:1.5}
.city-grid{display:grid;grid-template-columns:155px 170px 123px;margin-top:10px}
.city-grid li{font-size:12px;color:var(--ink);height:24px;padding-left:12px;position:relative;white-space:nowrap}
.city-grid li::before{content:"";position:absolute;left:0;top:8px;width:4px;height:4px;border-radius:50%;background:var(--ink)}
.cities .note{font-size:12px;color:var(--ink);margin-top:8px}
.cities hr{border:0;border-top:1px solid var(--line);margin:14px -20px 18px}
.cities .types{font-size:13px;color:#555;line-height:1.5}
.bullets{margin-top:10px}
.bullets li{font-size:13px;color:var(--ink);height:26px;padding-left:14px;position:relative}
.bullets li::before{content:"";position:absolute;left:0;top:8px;width:5px;height:5px;border-radius:50%;background:var(--ink)}

.archive{top:2194px;height:202px;padding:18px 20px;display:flex;gap:22px}
.archive ul li{font-size:13px;color:var(--ink);height:29px}
.archive .photo{width:310px;height:170px;background:linear-gradient(180deg,#4f8fd8 0%,#9ac3ee 45%,#c8b8a4 60%,#5f9a3c 85%)}
.gallery{top:2194px;height:202px;background:#fff;padding:14px 22px}
.gallery .bullets{margin-top:0}
.gallery .row{display:flex;gap:8px;margin-top:10px}
.gallery .photo{width:187px;height:140px}

/* footer */
.site-footer{position:absolute;left:0;top:2443px;width:1200px;height:244px;background:var(--footer);color:var(--footer-text)}
.fcol{position:absolute;top:34px}
.fcol h4{font-size:12px;font-weight:600;color:#fff;letter-spacing:.3px;margin-bottom:6px}
.fcol li{font-size:12px;height:19px;padding-left:10px;position:relative;white-space:nowrap}
.fcol li::before{content:"";position:absolute;left:0;top:8px;width:3px;height:3px;background:var(--footer-text);border-radius:50%}
.fcol .two{display:grid;grid-template-columns:120px 100px;grid-template-rows:repeat(4,19px);grid-auto-flow:column}
.fdivider{position:absolute;top:30px;width:1px;height:118px;background:#444}
.newsletter-input{display:flex;width:156px;height:28px;margin-top:6px}
.newsletter-input span{flex:1;background:#fff;color:#999;font-size:12px;padding:5px 8px}
.newsletter-input b{width:32px;background:#999;display:flex;align-items:center;justify-content:center}
.fsocial{display:flex;gap:8px;margin-top:12px}
.footer-line{position:absolute;left:98px;top:168px;width:1002px;border-top:1px solid #444}
.copyright{position:absolute;left:102px;top:196px;font-size:12px}
.footer-icons{position:absolute;right:100px;top:190px;display:flex;gap:10px}
.footer-icons span{width:28px;height:28px;border:1px solid #aaa;border-radius:50%;display:flex;align-items:center;justify-content:center}
</style>
</head>
<body>

<header class="site-header">
  <a class="brand" href="#"><span class="brand-mark"></span>quickdeedsale.com</a>
  <div class="call">
    <span class="call-label">Call us <small>Nights and weekends ok</small></span>
    <span class="call-number">555-014-2287</span>
    <span class="call-icon"><svg width="16" height="16" viewBox="0 0 24 24"><path d="M6.6 10.8a15 15 0 0 0 6.6 6.6l2.2-2.2a1 1 0 0 1 1-.25 11 11 0 0 0 3.6.6 1 1 0 0 1 1 1V20a1 1 0 0 1-1 1A17 17 0 0 1 3 4a1 1 0 0 1 1-1h3.5a1 1 0 0 1 1 1 11 11 0 0 0 .6 3.6 1 1 0 0 1-.25 1z" fill="#888"/></svg></span>
  </div>
  <nav class="main-nav">
    <a class="active" href="#">Sell Your Home</a><a href="#">How it works</a><a href="#">Stop foreclosure</a><a href="#">Probate</a><a href="#">Contact</a>
  </nav>
</header>

<section class="hero" role="img" aria-label="Photo of a single-storey white house with hedges under a blue sky">
  <span class="hero-arrow prev"><svg width="10" height="18" viewBox="0 0 10 18"><path d="M9 1 1 9l8 8" stroke="#fff" stroke-width="2" fill="none"/></svg></span>
  <span class="hero-arrow next"><svg width="10" height="18" viewBox="0 0 10 18"><path d="m1 1 8 8-8 8" stroke="#fff" stroke-width="2" fill="none"/></svg></span>
  <div class="hero-caption">
    <p>Sell your home for cash in 8 days</p>
    <p class="accent">We buy Houses Nationwide.</p>
  </div>
</section>

<section class="panel col-left benefits">
  <h2 class="red">These are the benefits of selling your home to us.</h2>
  <ul class="benefit-list">
    <li><svg width="16" height="16" viewBox="0 0 16 16"><rect x="1" y="3" width="14" height="12" fill="none" stroke="#333" stroke-width="1.5"/><path d="M1 6h14M5 1v4M11 1v4" stroke="#333" stroke-width="1.5"/></svg>You pick the closing date</li>
    <li><svg width="18" height="14" viewBox="0 0 18 14"><rect x="1" y="2" width="16" height="10" fill="none" stroke="#333" stroke-width="1.5"/><circle cx="9" cy="7" r="2.5" fill="#333"/></svg>You pay NO commissions or fees</li>
    <li><svg width="16" height="15" viewBox="0 0 16 15"><path d="M8 1 1 7.5h2V14h4v-4h2v4h4V7.5h2z" fill="#333"/></svg>You don't have to paint, clean or make repairs</li>
  </ul>
  <p class="video-intro">Watch to see our president Grant explain how easy it is to sell to us.</p>
  <div class="video" role="img" aria-label="Video still of the company president speaking in front of a house">
    <svg width="60" height="60" viewBox="0 0 60 60"><circle cx="30" cy="30" r="29" fill="rgba(0,0,0,.55)"/><path d="M24 18v24l19-12z" fill="#fff"/></svg>
  </div>
</section>

<section class="lead-form">
  <div class="form-ribbon"><strong>Yes, I want to sell my home fast!</strong><span>Get a no obligation written offer in 36 hours</span></div>
  <div class="fields">
    <div class="field">Your Name</div>
    <div class="field">Your Phone Number</div>
    <div class="field">Your E-mail Address</div>
    <div class="field">Property Address including City, State and Zip Code</div>
    <div class="field">Repairs needed if any</div>
    <div class="field">Asking price</div>
    <div class="field">Comments</div>
  </div>
  <div class="submit">SUBMIT, TO GET STARTED SELLING YOUR HOME FAST. <svg width="12" height="10" viewBox="0 0 12 10"><path d="m1 1 4 4-4 4M7 1l4 4-4 4" stroke="#fff" stroke-width="1.5" fill="none"/></svg></div>
</section>

<section class="panel col-left selling">
  <h1>Sell your home or house fast for cash to a professional investor company. We buy Houses and close quickly.</h1>
  <p class="lead">Selling a home on your own has never been easier. From Orlando to Greensboro - and all points in between- you can sell your home today without any hassles. Call 1-800-555-0148 or fill out the form below to get a written offer on your home in just 36 hours. Sell today online to people that care.</p>
  <hr>
  <h2 class="red">If you need to sell a home fast because of:</h2>
  <ul class="reasons">
    <li>Divorce or Bankruptcy</li>
    <li>Foreclosure</li>
    <li>Landlord problems - evictions with tenants okay</li>
    <li>Inherited property in probate</li>
    <li>Termites, mold, flood or fire damage, leaky roof</li>
    <li>Moving or can't afford mortgage payments</li>
  </ul>
  <p class="help">We Can Help.<br>We are the fastest home buyers around.</p>
</section>

<section class="panel col-right contact-strip">
  <div class="privacy">Our Privacy Policy <span class="dot" style="background:var(--deep-blue)"></span><span class="dot" style="background:var(--sky)"></span><span class="dot" style="background:#333"></span></div>
  <hr>
  <p class="hours">Call us 8am to 10 pm Eastern time. We answer our phones.</p>
</section>

<section class="panel col-right testimonials">
  <h2 class="red" style="font-size:16px">Home Seller Testimonials</h2>
  <blockquote>I just wanted to thank you for buying my home in Winter Park. You made it fast and easy and kept me well informed the whole way.</blockquote>
  <div class="author"><span>Dana Whitfield – Winter Park</span><small>More Testimonials</small></div>
</section>

<section class="panel col-right about">
  <div class="portrait" role="img" aria-label="Portrait photo of the company owner"></div>
  <div>
    <h2 class="red" style="font-size:16px">About us</h2>
    <p>Owned and operated in Orlando Florida since 2001. Oldest Continuous operated website in</p>
  </div>
</section>

<article class="panel col-left listing" style="top:1630px">
  <div class="photo" role="img" aria-label="Photo of a modern two-storey house at dusk" style="background:linear-gradient(180deg,#6a8fc4,#3b4b66 60%,#2a2f38)"></div>
  <div><h3>Pellentesque convallis molestie enim sit amet efficitur euismod iaculis mauris</h3><p>Fusce vitae lectus sit amet mi pulvinar maximus. Aenean placerat, nibh vel accumsan aliquet, magna nibh accumsan nibh, ac tempus nunc ipsum ac</p><span class="more">MORE</span></div>
</article>
<article class="panel col-left listing" style="top:1812px">
  <div class="photo" role="img" aria-label="Photo of a modern apartment building against a blue sky" style="background:linear-gradient(180deg,#2f6fc9,#9ab8d9 55%,#8a5d3a)"></div>
  <div><h3>Pellentesque convallis molestie enim sit amet efficitur euismod iaculis mauris</h3><p>Fusce vitae lectus sit amet mi pulvinar maximus. Aenean placerat, nibh vel accumsan aliquet, magna nibh accumsan nibh, ac tempus nunc ipsum ac</p><span class="more">MORE</span></div>
</article>
<article class="panel col-left listing" style="top:1995px">
  <div class="photo" role="img" aria-label="Photo of a lit modern villa with a pool at night" style="background:linear-gradient(180deg,#2c3a52,#6b5a44 55%,#2a4a6a)"></div>
  <div><h3>Pellentesque convallis molestie enim sit amet efficitur euismod iaculis mauris</h3><p>Fusce vitae lectus sit amet mi pulvinar maximus. Aenean placerat, nibh vel accumsan aliquet, magna nibh accumsan nibh, ac tempus nunc ipsum ac</p><span class="more">MORE</span></div>
</article>

<section class="panel col-right cities">
  <h2 class="red" style="font-size:16px">Some of the cities where we buy houses. Not all are listed.</h2>
  <p class="intro">These are the cities where we have an affiliate where you can sell a home fast or quickly and we buy homes:</p>
  <ul class="city-grid">
    <li>Orlando</li><li>Camden</li><li>Charleston SC</li>
    <li>Jacksonville Ft</li><li>Atlanta</li><li>Flint RochesterLake</li>
    <li>Myers Tampa St</li><li>Valdosta Houston</li><li>Florida Wilmington</li>
    <li>Pete Gainesville</li><li>Detroit Phoenix</li><li>Columbia Titusville</li>
    <li>Tallahassee</li><li>Seattle</li><li style="visibility:hidden"></li>
    <li>Melbourne</li><li>Tacoma Portland</li><li style="visibility:hidden"></li>
    <li>West Palm Beach</li><li>Charlotte Cincinnati</li><li style="visibility:hidden"></li>
    <li>Apopka Deland Kissimmee</li><li>San Antonio</li><li style="visibility:hidden"></li>
    <li>Lakeland</li><li>Harrisburg Virginia Beach</li><li style="visibility:hidden"></li>
    <li>Ocala Chicago</li><li>Virginia Homes</li><li style="visibility:hidden"></li>
    <li>Philadelphia</li><li>Greensboro</li><li style="visibility:hidden"></li>
  </ul>
  <p class="note">If you don't see your city, we still probably buy homes there.</p>
  <hr>
  <p class="types">These are the types of real estate that we buy: We buy nice houses and outdated problem homes.</p>
  <ul class="bullets">
    <li>We buy in great neighborhoods and not so nice.</li>
    <li>We buy block homes and frame homes.</li>
  </ul>
</section>

<section class="panel col-left archive">
  <ul>
    <li>Archives</li><li>Sell my house</li><li>Fast cash for</li><li>homes</li><li>We buy houses</li><li>Real Estate</li>
  </ul>
  <div class="photo" role="img" aria-label="Photo of a large suburban house with a green lawn"></div>
</section>

<section class="panel col-right gallery">
  <ul class="bullets"><li>We buy nice pretty houses and some ugly ones as well.</li></ul>
  <div class="row">
    <div class="photo" role="img" aria-label="Photo of a house with a driveway among trees" style="background:linear-gradient(180deg,#a7c3a0,#4f7a3e 50%,#9a9a90)"></div>
    <div class="photo" role="img" aria-label="Photo of a single-storey house with a garage among trees" style="background:linear-gradient(180deg,#5d7f4a,#3b5a30 55%,#8c8c84)"></div>
  </div>
</section>

<footer class="site-footer">
  <div class="fcol" style="left:102px">
    <h4>QUICK LINKS</h4>
    <ul class="two"><li>Home</li><li>Sell Your Home</li><li>How it works</li><li>Stop foreclosure</li><li>Probate</li><li>Contact</li></ul>
  </div>
  <span class="fdivider" style="left:360px"></span>
  <div class="fcol" style="left:385px"><h4>MORE</h4><ul><li>FAQ</li><li>Support Center</li><li>Blog</li><li>Register</li></ul></div>
  <span class="fdivider" style="left:548px"></span>
  <div class="fcol" style="left:573px"><h4>MORE</h4><ul><li>FAQ</li><li>Support Center</li><li>Blog</li><li>Register</li></ul></div>
  <span class="fdivider" style="left:736px"></span>
  <div class="fcol" style="left:761px"><h4>MORE</h4><ul><li>FAQ</li><li>Support Center</li><li>Blog</li><li>Register</li></ul></div>
  <span class="fdivider" style="left:918px"></span>
  <div class="fcol" style="left:942px">
    <h4>NEWSLETTER</h4>
    <div class="newsletter-input"><span>E-mail</span><b><svg width="10" height="12" viewBox="0 0 10 12"><path d="M1 1l8 5-8 5z" fill="#fff"/></svg></b></div>
    <div class="fsocial"><span class="dot" style="background:var(--deep-blue)"></span><span class="dot" style="background:var(--sky)"></span><span class="dot" style="background:#555"></span><span class="dot" style="background:var(--red)"></span></div>
  </div>
  <div class="footer-line"></div>
  <p class="copyright">Copyright © 2015 quickdeedsale.com. All rights reserved.</p>
  <div class="footer-icons">
    <span><svg width="14" height="10" viewBox="0 0 14 10"><rect x="1" y="1" width="12" height="8" fill="none" stroke="#ccc"/><path d="m1 1 6 4 6-4" stroke="#ccc" fill="none"/></svg></span>
    <span><svg width="12" height="12" viewBox="0 0 12 12"><path d="M6 11V1M1 6l5-5 5 5" stroke="#ccc" stroke-width="1.5" fill="none"/></svg></span>
  </div>
</footer>

</body>
</html>
```